The Harbourlight Aid Trust needs a graphic of their innovation approach

What we need?
- we have designed a new innovation approach (see attached). An innovation approach is the process one goes through in order to design and launch a new product or service.
- This new graphic will be used in meetings to help others understand what innovation is and how we do it. It will also be used in training sessions and be the starting point for innovation training materials we are creating
- We have created this draft graphic by copying and pasting new words over another charities innovation process
- We would like you to use your design magic and create our very own innovation process graphic. We would like it to be neat, simple, non fussy, easy to understand /read and in line with our brand colours
Attached:
1. PowerPoint:
- Slide 1: our innovation process
- Slide 2 explanation of process to bring it to life
- Slide 3&4: brand colours
- Slide 5: inspiration / examples of other processes we like the look of
2. Typeface brand guidelines
We can't wait to see what you come up with! Thank you :)
Target Market(s)
internal employees
Industry/Entity Type
Charity
Colors
Designer to choose colors to be used in the design.
Look and feel
Each slider illustrates characteristics of the customer's brand and the style your logo design should communicate.

```html
<!DOCTYPE html>
<html lang="en">
<head>
<meta charset="utf-8">
<title>Harbourlight Aid Trust – Innovation Approach</title>
<link rel="stylesheet" href="https://fonts.googleapis.com/css2?family=Arimo:wght@400;700&display=swap">
<style>
  :root {
    --discover: #e31b17;
    --discover-soft: #f08480;
    --define: #5b9bc6;
    --define-soft: #a9c8de;
    --deliver: #06923e;
    --deliver-soft: #7cc79a;
    --paper: #ffffff;
  }
  html, body {
    margin: 0;
    padding: 0;
    width: 1200px;
    height: 1094px;
    overflow: hidden;
    background: var(--paper);
  }
  .process-map {
    display: block;
    width: 1200px;
    height: 1094px;
    font-family: "Arimo", Arial, sans-serif;
  }
  .flow { fill: none; stroke-width: 30; }
  .flow--discover { stroke: var(--discover); }
  .flow--define { stroke: var(--define); }
  .flow--deliver { stroke: var(--deliver); }
  .head--discover { fill: var(--discover); }
  .head--define { fill: var(--define); }
  .head--deliver { fill: var(--deliver); }
  .loop { fill: none; stroke-width: 4; stroke-dasharray: 5 5; }
  .loop--discover { stroke: var(--discover-soft); }
  .loop--define { stroke: var(--define-soft); }
  .loop--deliver { stroke: var(--deliver-soft); }
  .loop-head--discover { fill: var(--discover-soft); }
  .loop-head--define { fill: var(--define-soft); }
  .loop-head--deliver { fill: var(--deliver-soft); }
  .stage { fill: var(--paper); stroke-width: 9; }
  .stage--discover { stroke: var(--discover); }
  .stage--define { stroke: var(--define); }
  .stage--deliver { stroke: var(--deliver); }
  .stage-label { font-size: 16px; text-anchor: middle; }
  .step-label { font-size: 16px; font-weight: 700; fill: #fff; text-anchor: middle; }
  .phase-title { font-size: 30px; text-anchor: middle; }
  .text--discover { fill: var(--discover); }
  .text--define { fill: var(--define); }
  .text--deliver { fill: var(--deliver); }
</style>
</head>
<body>
<svg class="process-map" viewBox="0 0 1166 1050" preserveAspectRatio="xMidYMid meet" role="img" aria-label="Harbourlight Aid Trust innovation approach: Discover, Define, Deliver">
  <!-- feedback loops -->
  <g class="feedback-loops">
    <path class="loop loop--discover" d="M560,112 H345 Q298,112 298,155 V318"/>
    <polygon class="loop-head--discover" points="289,318 307,318 298,330"/>
    <path class="loop loop--define" d="M800,343 H668"/>
    <path class="loop loop--discover" d="M668,343 V224"/>
    <polygon class="loop-head--discover" points="659,224 677,224 668,212"/>
    <path class="loop loop--define" d="M690,713 H866 Q906,713 906,673 V462"/>
    <polygon class="loop-head--define" points="897,462 915,462 906,450"/>
    <path class="loop loop--deliver" d="M402,945 H628 Q668,945 668,905 V755"/>
    <polygon class="loop-head--deliver" points="659,755 677,755 668,743"/>
  </g>

  <!-- main flow -->
  <g class="main-flow">
    <path class="flow flow--discover" d="M338,325 V190 Q338,147 381,147 H542"/>
    <polygon class="head--discover" points="540,117 571,147 540,177"/>

    <path class="flow flow--define" d="M629,335 Q629,380 674,380 H778"/>
    <path class="flow flow--discover" d="M629,215 V345"/>
    <polygon class="head--define" points="775,351 808,380 775,409"/>

    <path class="flow flow--define" d="M868,452 V630 Q868,675 823,675 H712"/>
    <polygon class="head--define" points="716,645 683,675 716,705"/>

    <path class="flow flow--deliver" d="M628,748 V863 Q628,908 583,908 H425"/>
    <polygon class="head--deliver" points="429,879 395,908 429,937"/>

    <rect class="head--deliver" x="323" y="658" width="30" height="182"/>
    <polygon class="head--deliver" points="308,661 338,630 368,661"/>
  </g>

  <!-- step labels -->
  <g class="step-labels">
    <text class="step-label" x="462" y="153">INSIGHT</text>
    <text class="step-label" transform="translate(636,288) rotate(-90)">IDEATE</text>
    <text class="step-label" x="705" y="386">(IN)VALIDATE</text>
    <text class="step-label" x="768" y="681">TEST</text>
    <text class="step-label" x="516" y="914">DELIVERY PLAN</text>
  </g>

  <!-- stages -->
  <g class="stages">
    <circle class="stage stage--discover" cx="338" cy="393" r="70"/>
    <text class="stage-label text--discover" x="338" y="399">CHALLENGE</text>
    <circle class="stage stage--discover" cx="629" cy="148" r="70"/>
    <text class="stage-label text--discover" x="629" y="146">OPPORTUNITY</text>
    <text class="stage-label text--discover" x="629" y="166">STATEMENT</text>
    <circle class="stage stage--define" cx="866" cy="383" r="70"/>
    <text class="stage-label text--define" x="866" y="389">CONCEPTS</text>
    <circle class="stage stage--deliver" cx="628" cy="678" r="70"/>
    <text class="stage-label text--deliver" x="628" y="684">SOLUTION</text>
    <circle class="stage stage--deliver" cx="337" cy="908" r="70"/>
    <text class="stage-label text--deliver" x="337" y="914">LAUNCH</text>
  </g>

  <!-- phase titles -->
  <g class="phase-titles">
    <text class="phase-title text--discover" x="484" y="273" font-weight="700">DISCOVER</text>
    <text class="phase-title text--define" x="745" y="541">DEFINE</text>
    <text class="phase-title text--deliver" x="481" y="792">DELIVER</text>
  </g>
</svg>
</body>
</html>
```